Firm Stationery Design

I need a design for stationery, including: Stationery First Page, Stationery Second Sheet, Envelope, Mailing Label for Flat Envelopes, and Business Cards

```html
<!DOCTYPE html>
<html lang="en">
<head>
<meta charset="utf-8">
<title>Marlow Law LLC — Envelope</title>
<link rel="stylesheet" href="https://fonts.googleapis.com/css2?family=Montserrat:wght@400;700&display=swap">
<style>
  :root {
    --backdrop: #3b3b3b;
    --paper: #fbfbfa;
    --ink: #111111;
    --accent: #f39a0f;
    --window-light: #e4e4e4;
    --window-mid: #cfcfcf;
    --flap: #121212;
  }
  * { box-sizing: border-box; margin: 0; padding: 0; }
  html, body {
    width: 1200px;
    height: 800px;
    overflow: hidden;
    background: var(--backdrop);
    font-family: "Montserrat", sans-serif;
  }
  .canvas {
    position: relative;
    width: 1200px;
    height: 800px;
  }
  .envelope {
    position: absolute;
    top: 270px;
    width: 520px;
    height: 260px;
    background: var(--paper);
    box-shadow: 0 18px 30px rgba(0, 0, 0, 0.35);
    overflow: hidden;
  }
  .envelope--front { left: 50px; }
  .envelope--back { left: 630px; }

  .brand {
    position: absolute;
    top: 30px;
    left: 32px;
    display: flex;
    align-items: center;
    gap: 8px;
  }
  .brand__mark {
    width: 14px;
    height: 14px;
    background: var(--accent);
  }
  .brand__name {
    font-weight: 700;
    font-size: 15px;
    letter-spacing: 1.5px;
    color: var(--ink);
    text-transform: uppercase;
  }

  .return-address {
    position: absolute;
    left: 32px;
    bottom: 44px;
    font-size: 10px;
    line-height: 1.35;
    color: var(--ink);
  }

  .address-window {
    position: absolute;
    right: 40px;
    bottom: 28px;
    width: 140px;
    height: 70px;
    background: linear-gradient(100deg, var(--window-mid) 0%, var(--window-light) 55%, var(--window-mid) 100%);
  }

  .flap {
    position: absolute;
    top: 0;
    left: 0;
    width: 520px;
    height: 120px;
  }
  .flap__name {
    position: absolute;
    top: 48px;
    left: 0;
    width: 520px;
    text-align: center;
    font-weight: 700;
    font-size: 18px;
    letter-spacing: 2px;
    color: var(--paper);
    text-transform: uppercase;
  }
</style>
</head>
<body>
  <main class="canvas">
    <section class="envelope envelope--front" aria-label="Envelope front">
      <div class="brand">
        <span class="brand__mark" aria-hidden="true"></span>
        <span class="brand__name">Marlow Law LLC</span>
      </div>
      <address class="return-address" style="font-style: normal;">
        Your address, City<br>
        State, Zip 1234
      </address>
      <div class="address-window" aria-hidden="true"></div>
    </section>

    <section class="envelope envelope--back" aria-label="Envelope back">
      <svg class="flap" viewBox="0 0 520 120" aria-hidden="true">
        <path d="M0 0 H520 V0 L480 100 Q472 120 450 120 H70 Q48 120 40 100 L0 0 Z" fill="var(--flap)"/>
      </svg>
      <span class="flap__name">Marlow Law LLC</span>
    </section>
  </main>
</body>
</html>
```